Business Card Design for Training Business

Clear Path Coaching is a new business that delivers training and other services with a focus on topics related to mental health and wellbeing, for example, Wellmind Response Course, Resilience etc. We have a strong focus on evidence-based psychology and neuroscience. I have a logo which I will upload with the brief, so please consider colours that work well with the logo.
Target Market(s)
Adults, workplaces (particularly government and not-for-profits)
Industry/Entity Type
Business
Contact Information for Business Card
Head Strong TrainingSamantha SellwoodDirector0438 770 850sam@headstrongtraining.com.auwww.headstrongtraining.com.au

```html
<!DOCTYPE html>
<html lang="en">
<head>
<meta charset="utf-8">
<title>Clear Path Coaching — Business Card</title>
<link rel="stylesheet" href="https://fonts.googleapis.com/css2?family=Open+Sans:wght@400;600;700&family=Raleway:wght@300&display=swap">
<style>
  :root {
    --backdrop: #e6e1d8;
    --card-white: #f7f7f7;
    --card-black: #0b0b0c;
    --teal: #2fc4c6;
    --ink-light: #ffffff;
    --logo-grey: #9a9a9a;
    --shadow: rgba(40, 30, 20, 0.25);
  }
  * { box-sizing: border-box; margin: 0; padding: 0; }
  html, body {
    width: 1200px;
    height: 1022px;
    overflow: hidden;
    background: var(--backdrop);
  }
  .sheet {
    position: relative;
    width: 1200px;
    height: 1022px;
  }
  .card {
    position: absolute;
    left: 220px;
    width: 760px;
    height: 462px;
    border-radius: 26px;
    overflow: hidden;
    background: var(--card-white);
    box-shadow: 0 10px 30px var(--shadow);
  }
  .card--contact { top: 36px; }
  .card--brand { top: 528px; }

  .card__shape {
    position: absolute;
    inset: 0;
    width: 760px;
    height: 462px;
  }

  .contact {
    position: absolute;
    top: 44px;
    right: 40px;
    text-align: right;
    font-family: "Open Sans", sans-serif;
    color: var(--ink-light);
  }
  .contact__name {
    font-size: 40px;
    font-weight: 700;
    line-height: 1.1;
    margin-right: 44px;
  }
  .contact__role {
    font-size: 22px;
    font-weight: 400;
    color: var(--teal);
    margin: 2px 44px 12px 0;
  }
  .contact__line {
    display: flex;
    justify-content: flex-end;
    align-items: center;
    gap: 18px;
    font-size: 21px;
    line-height: 35px;
  }
  .contact__icon {
    width: 24px;
    height: 24px;
    flex: none;
  }

  .brand {
    position: absolute;
    display: flex;
    align-items: center;
    gap: 22px;
  }
  .brand__mark {
    flex: none;
    border: 3px solid var(--teal);
    border-radius: 50%;
  }
  .brand__name {
    font-family: "Raleway", sans-serif;
    font-weight: 300;
    color: var(--logo-grey);
    letter-spacing: 0.08em;
    text-transform: uppercase;
    line-height: 1.1;
  }
  .card--contact .brand { left: 56px; bottom: 48px; }
  .card--contact .brand__mark { width: 86px; height: 86px; }
  .card--contact .brand__name { font-size: 30px; }

  .card--brand .brand {
    left: 50%;
    top: 50%;
    transform: translate(-50%, -50%);
  }
  .card--brand .brand__mark { width: 110px; height: 110px; }
  .card--brand .brand__name { font-size: 40px; white-space: nowrap; }
</style>
</head>
<body>
<main class="sheet">

  <section class="card card--contact" aria-label="Business card, contact side">
    <svg class="card__shape" viewBox="0 0 760 462" aria-hidden="true">
      <path d="M0 0 H760 V250 C560 330 200 330 0 170 Z" fill="var(--card-black)"/>
      <path d="M760 250 C560 330 200 330 0 170" fill="none" stroke="var(--teal)" stroke-width="6"/>
    </svg>

    <div class="contact">
      <p class="contact__name">Rebecca Tanfield</p>
      <p class="contact__role">Director</p>
      <p class="contact__line">
        <span>0491 362 517</span>
        <svg class="contact__icon" viewBox="0 0 24 24" aria-label="Phone">
          <path d="M6.5 3 L9.5 3 L11 8 L8.8 9.6 C9.8 12 11.9 14.2 14.4 15.2 L16 13 L21 14.5 L21 17.5 C21 19.4 19.4 21 17.5 21 C9.5 21 3 14.5 3 6.5 C3 4.6 4.6 3 6.5 3 Z" fill="var(--teal)"/>
        </svg>
      </p>
      <p class="contact__line">
        <span>bec@clearpathcoaching.example.au</span>
        <svg class="contact__icon" viewBox="0 0 24 24" aria-label="Email">
          <rect x="3" y="5.5" width="18" height="13" rx="1.5" fill="none" stroke="var(--teal)" stroke-width="2"/>
          <path d="M3.5 6.5 L12 13 L20.5 6.5" fill="none" stroke="var(--teal)" stroke-width="2"/>
        </svg>
      </p>
      <p class="contact__line">
        <span>www.clearpathcoaching.example.au</span>
        <svg class="contact__icon" viewBox="0 0 24 24" aria-label="Website">
          <circle cx="12" cy="12" r="9" fill="none" stroke="var(--teal)" stroke-width="2"/>
          <ellipse cx="12" cy="12" rx="4" ry="9" fill="none" stroke="var(--teal)" stroke-width="1.6"/>
          <path d="M3 12 H21 M5 7.5 H19 M5 16.5 H19" stroke="var(--teal)" stroke-width="1.6"/>
        </svg>
      </p>
    </div>

    <div class="brand">
      <span class="brand__mark" aria-hidden="true"></span>
      <p class="brand__name">Clear Path Coaching</p>
    </div>
  </section>

  <section class="card card--brand" aria-label="Business card, brand side">
    <div class="brand">
      <span class="brand__mark" aria-hidden="true"></span>
      <p class="brand__name">Clear Path Coaching</p>
    </div>
  </section>

</main>
</body>
</html>
```